VORLE Diagnostics Pooling One Sheet

The process and concept for pooling is to target large populations of people; i.e. a school, prison, employer (where people are isolated by pods), then to test them all in one controllable group. By breaking down the pool size (ideally is 12 or 16 max) then when a positive pool pops up, the entity has the lab automatically reflex to test the whole pool to determine who is positive. During that exchange, several workflows could take place from the population that was being tested. This type of pooled testing is called Surveillance testing ,when it reflects, then it goes to Screening or Diagnostic testing.

The workflow is:
School/employer collects all patient information captured on a requisition form or electronically (w signature) and DOES NOT send to VORLE
School/employer collects individual specimens and labels them with a unique bar code (non-repeating and can include the DOB)
School/employer is responsible for housing and managing all the unique patient information for each individual specimen
School/employer delivers specimens to VORLE and School/employer directs VORLE what specimens are in what designated pool (one pool size for entire project)
When a pool is positive, VORLE notifies School/employer
When reflex testing in indicated for client, School/employer submits to VORLE on demand all patient information needed to process the reflexed option
VORLE reports back to School/employer in 12 hours the results of the retest
https://www.healthregistry-example.org/medical-devices/coronavirus-covid-19-and-medical-devices/pooled-sample-testing-and-screening-testing-covid-19
https://www.testmere.com/coronavirus-disease-covid-19/news/testmere-receives-authorization-covid-19-sample-pooling

Target Market(s)

Schools, Universities, Employers

Font styles to use
Sans Serif

Colors
85acd3
85cae6
34a6d7

Requirements
Must have
• VORLE branded along with an elegant yet clinical feel. have all contact information for VORLE Diagnostics. Go to www.vorledx.com for all info

```html
<!DOCTYPE html>
<html lang="en">
<head>
<meta charset="utf-8">
<title>VORLE Diagnostics – Pooled Sample Testing</title>
<link href="https://fonts.googleapis.com/css2?family=Montserrat:wght@700;800&family=Roboto+Condensed:wght@400;500;700&display=swap" rel="stylesheet">
<style>
  :root{
    --teal:#3f9fb3;
    --teal-dark:#2f8596;
    --teal-light:#85cae6;
    --url-accent:#4fb4c8;
    --ink:#16191c;
    --footer-dark:#393c3f;
    --page:#e7e9ea;
    --rule:#9aa3a8;
    --body-text:#3a3f44;
  }
  *{margin:0;padding:0;box-sizing:border-box}
  html,body{width:1200px;height:800px;overflow:hidden}
  body{background:var(--page);font-family:"Roboto Condensed",Arial,sans-serif}
  .sheet-wrap{position:absolute;left:300px;top:10px;width:600px;height:780px}
  .sheet{position:absolute;left:0;top:0;width:612px;height:795px;background:#fff;
    transform:scale(0.981);transform-origin:0 0;overflow:hidden;box-shadow:0 4px 14px rgba(0,0,0,.18)}
  .abs{position:absolute}

  .hero-photo{left:0;top:51px;width:612px;height:310px;
    background:linear-gradient(90deg,#c9d3dc 0%,#dfe6ec 35%,#eef2f5 55%,#d7e3ea 75%,#bfd6e2 100%)}
  .header-shape{left:0;top:0}
  .brand{left:20px;top:29px;display:flex;align-items:center;gap:8px}
  .brand-mark{width:30px;height:30px;background:var(--teal-dark)}
  .brand-name{font-weight:700;font-size:20px;line-height:30px;color:var(--teal-dark);letter-spacing:.2px}
  .title-tab-text{left:340px;width:258px;top:15px;text-align:right;color:#fff;
    font-weight:700;font-size:21px;line-height:24px;letter-spacing:.1px;white-space:nowrap}

  .hero-title{left:20px;top:128px;font-family:"Montserrat",sans-serif;font-weight:800;
    font-size:37px;line-height:41px;color:var(--ink);letter-spacing:1px}

  .intro{color:#fff;font-size:9px;line-height:13px;letter-spacing:-.1px}
  .intro .line{display:block;text-align:justify;text-align-last:justify;white-space:nowrap}
  .intro .line.last{text-align-last:left}
  .intro-top{left:20px;top:316px;width:290px}
  .intro-wide{left:20px;top:369px;width:580px}

  .workflow-label{left:20px;top:556px;font-weight:700;font-size:8.5px;color:var(--teal)}
  .step-text{width:112px;font-size:7.4px;line-height:9px;color:var(--body-text);
    text-align:justify;border-left:1px solid var(--rule);padding-left:4px}
  .step-icon{width:52px;height:52px}

  .footer-cta{left:20px;top:763px;color:#fff;font-size:13.5px;line-height:20px;letter-spacing:.2px}
  .footer-url{left:396px;top:762px;display:flex;align-items:center;gap:7px;
    color:#fff;font-family:"Montserrat",sans-serif;font-weight:700;font-size:15.5px;line-height:20px}
  .footer-url .accent{color:var(--url-accent)}
</style>
</head>
<body>
<div class="sheet-wrap">
<main class="sheet">

  <!-- hero -->
  <div class="abs hero-photo" role="img" aria-label="Laboratory photograph of a technician in protective cap, mask and gloves pipetting a sample"></div>

  <svg class="abs header-shape" width="612" height="86" viewBox="0 0 612 86" aria-hidden="true">
    <polygon points="0,0 612,0 612,51 322,51 307,85 0,85" fill="#fff"/>
    <polygon points="337,0 612,0 612,51 322,51" fill="var(--teal)"/>
  </svg>

  <div class="abs brand">
    <span class="brand-mark"></span>
    <span class="brand-name">VORLE Diagnostics</span>
  </div>
  <div class="abs title-tab-text">POOLED SAMPLE TESTING</div>

  <h1 class="abs hero-title">RAPID<br>COVID-19<br>TESTING</h1>

  <!-- intro band -->
  <svg class="abs" width="612" height="124" viewBox="0 0 612 124" style="left:0;top:296px" aria-hidden="true">
    <polygon points="0,0 318,0 380,62 612,62 612,124 0,124" fill="var(--teal)"/>
  </svg>
  <p class="abs intro intro-top">
    <span class="line">The process and concept for pooling is to target large populations</span>
    <span class="line">of people; i.e. a school, prison, employer (where people are isolated</span>
    <span class="line">by pods), then to test them all in one controllable group. By breaking</span>
    <span class="line last">down the pool size (ideally is 12 or 16 max) then when a positive pool</span>
  </p>
  <p class="abs intro intro-wide">
    <span class="line">pops up, the entity has the lab automatically reflex to test the whole pool to determine who is positive. During that exchange, several</span>
    <span class="line">workflows could take place from the population that was being tested. This type of pooled testing is called Surveillance testing, when it</span>
    <span class="line last">reflects, then it goes to Screening or Diagnostic testing.</span>
  </p>

  <!-- workflow -->
  <div class="abs workflow-label">THE WORKFLOW</div>

  <svg class="abs" width="612" height="120" viewBox="0 0 612 120" style="left:0;top:516px" aria-hidden="true">
    <line x1="20" y1="60" x2="600" y2="60" stroke="var(--rule)" stroke-width="1"/>
    <g stroke="var(--rule)" stroke-width="1" fill="var(--teal)">
      <line x1="160" y1="40" x2="160" y2="60"/><circle cx="160" cy="46" r="2"/>
      <line x1="306" y1="40" x2="306" y2="60"/><circle cx="306" cy="46" r="2"/>
      <line x1="464" y1="40" x2="464" y2="60"/><circle cx="464" cy="46" r="2"/>
      <line x1="88" y1="60" x2="88" y2="80"/><circle cx="88" cy="70" r="2"/>
      <line x1="227" y1="60" x2="227" y2="80"/><circle cx="227" cy="70" r="2"/>
      <line x1="385" y1="60" x2="385" y2="80"/><circle cx="385" cy="70" r="2"/>
      <line x1="539" y1="60" x2="539" y2="80"/><circle cx="539" cy="70" r="2"/>
    </g>
  </svg>

  <!-- step texts, top row -->
  <p class="abs step-text" style="left:108px;top:450px">School / employer collects all patient information captured on a requisition form or electronically (w signature) and DOES NOT send to VORLE</p>
  <p class="abs step-text" style="left:254px;top:450px">School / employer collects individual specimens and labels them with a unique bar code (non-repeating and can include the DOB)</p>
  <p class="abs step-text" style="left:408px;top:452px">School / employer is responsible for housing and managing all the unique patient information for each individual specimen</p>

  <!-- step texts, bottom row -->
  <p class="abs step-text" style="left:32px;top:656px">School / employer delivers specimens to VORLE and School / employer directs VORLE what specimens are in what designated pool (one pool size for entire project)</p>
  <p class="abs step-text" style="left:170px;top:658px">When a pool is positive, VORLE notifies School/employer</p>
  <p class="abs step-text" style="left:327px;top:658px">When reflex testing in indicated for client, School / employer submits to VORLE on demand all patient information needed to process the reflexed option</p>
  <p class="abs step-text" style="left:482px;top:658px">VORLE reports back to School / employer in 12 hours the results of the retest</p>

  <!-- icons -->
  <svg class="abs step-icon" style="left:134px;top:502px" viewBox="-30 -30 60 60" aria-hidden="true">
    <polygon points="0,-27 23.4,-13.5 23.4,13.5 0,27 -23.4,13.5 -23.4,-13.5" fill="#fff" stroke="var(--teal)" stroke-width="2"/>
    <polygon points="0,-21 18.2,-10.5 18.2,10.5 0,21 -18.2,10.5 -18.2,-10.5" fill="var(--teal)"/>
    <g fill="none" stroke="#fff" stroke-width="1.6"><rect x="-7" y="-9" width="13" height="17"/><line x1="-4" y1="-4" x2="3" y2="-4"/><line x1="-4" y1="0" x2="3" y2="0"/><line x1="-4" y1="4" x2="1" y2="4"/><line x1="2" y1="8" x2="9" y2="1"/></g>
  </svg>
  <svg class="abs step-icon" style="left:280px;top:502px" viewBox="-30 -30 60 60" aria-hidden="true">
    <polygon points="0,-27 23.4,-13.5 23.4,13.5 0,27 -23.4,13.5 -23.4,-13.5" fill="#fff" stroke="var(--teal)" stroke-width="2"/>
    <polygon points="0,-21 18.2,-10.5 18.2,10.5 0,21 -18.2,10.5 -18.2,-10.5" fill="var(--teal)"/>
    <g fill="none" stroke="#fff" stroke-width="1.6"><polygon points="-9,-3 -3,-9 9,3 3,9"/><circle cx="-3" cy="-3" r="1.4" fill="#fff"/><line x1="-9" y1="-3" x2="-11" y2="-11"/></g>
  </svg>
  <svg class="abs step-icon" style="left:438px;top:502px" viewBox="-30 -30 60 60" aria-hidden="true">
    <polygon points="0,-27 23.4,-13.5 23.4,13.5 0,27 -23.4,13.5 -23.4,-13.5" fill="#fff" stroke="var(--teal)" stroke-width="2"/>
    <polygon points="0,-21 18.2,-10.5 18.2,10.5 0,21 -18.2,10.5 -18.2,-10.5" fill="var(--teal)"/>
    <g fill="none" stroke="#fff" stroke-width="1.6"><rect x="-7" y="-8" width="14" height="18"/><rect x="-3" y="-11" width="6" height="4" fill="#fff"/><line x1="-4" y1="-2" x2="4" y2="-2"/><line x1="-4" y1="2" x2="4" y2="2"/><line x1="-4" y1="6" x2="4" y2="6"/></g>
  </svg>
  <svg class="abs step-icon" style="left:62px;top:595px" viewBox="-30 -30 60 60" aria-hidden="true">
    <polygon points="0,-27 23.4,-13.5 23.4,13.5 0,27 -23.4,13.5 -23.4,-13.5" fill="#fff" stroke="var(--teal)" stroke-width="2"/>
    <polygon points="0,-21 18.2,-10.5 18.2,10.5 0,21 -18.2,10.5 -18.2,-10.5" fill="var(--teal)"/>
    <g fill="none" stroke="#fff" stroke-width="1.6"><line x1="-2" y1="-11" x2="3" y2="2"/><path d="M-5,3 a7,7 0 0 0 12,4"/><line x1="-9" y1="10" x2="9" y2="10"/><line x1="-6" y1="7" x2="-6" y2="10"/></g>
  </svg>
  <svg class="abs step-icon" style="left:201px;top:595px" viewBox="-30 -30 60 60" aria-hidden="true">
    <polygon points="0,-27 23.4,-13.5 23.4,13.5 0,27 -23.4,13.5 -23.4,-13.5" fill="#fff" stroke="var(--teal)" stroke-width="2"/>
    <polygon points="0,-21 18.2,-10.5 18.2,10.5 0,21 -18.2,10.5 -18.2,-10.5" fill="var(--teal)"/>
    <polyline points="-8,0 -2,6 9,-7" fill="none" stroke="#fff" stroke-width="2.4"/>
  </svg>
  <svg class="abs step-icon" style="left:359px;top:595px" viewBox="-30 -30 60 60" aria-hidden="true">
    <polygon points="0,-27 23.4,-13.5 23.4,13.5 0,27 -23.4,13.5 -23.4,-13.5" fill="#fff" stroke="var(--teal)" stroke-width="2"/>
    <polygon points="0,-21 18.2,-10.5 18.2,10.5 0,21 -18.2,10.5 -18.2,-10.5" fill="var(--teal)"/>
    <g fill="none" stroke="#fff" stroke-width="1.5"><circle cx="0" cy="-4" r="3"/><path d="M-5,6 a5,5 0 0 1 10,0"/><circle cx="-8" cy="-1" r="2.2"/><circle cx="8" cy="-1" r="2.2"/><path d="M-12,7 a4,4 0 0 1 6,-3"/><path d="M12,7 a4,4 0 0 0 -6,-3"/></g>
  </svg>
  <svg class="abs step-icon" style="left:513px;top:595px" viewBox="-30 -30 60 60" aria-hidden="true">
    <polygon points="0,-27 23.4,-13.5 23.4,13.5 0,27 -23.4,13.5 -23.4,-13.5" fill="#fff" stroke="var(--teal)" stroke-width="2"/>
    <polygon points="0,-21 18.2,-10.5 18.2,10.5 0,21 -18.2,10.5 -18.2,-10.5" fill="var(--teal)"/>
    <g fill="none" stroke="#fff" stroke-width="1.6"><circle cx="2" cy="2" r="8"/><line x1="2" y1="2" x2="2" y2="-3"/><line x1="2" y1="2" x2="5" y2="4"/><line x1="0" y1="-9" x2="4" y2="-9"/><line x1="-11" y1="-1" x2="-7" y2="-1"/><line x1="-12" y1="3" x2="-7" y2="3"/></g>
  </svg>

  <!-- footer -->
  <svg class="abs" width="612" height="42" viewBox="0 0 612 42" style="left:0;top:752px" aria-hidden="true">
    <rect x="0" y="0" width="612" height="42" fill="var(--footer-dark)"/>
    <polygon points="0,0 352,0 374,42 0,42" fill="var(--teal)"/>
  </svg>
  <div class="abs footer-cta">VISIT OUR WEBSITE FOR MORE INFORMATION</div>
  <div class="abs footer-url">
    <svg width="16" height="16" viewBox="-8 -8 16 16" aria-hidden="true"><g fill="none" stroke="#fff" stroke-width="1.4"><circle r="6.5"/><ellipse rx="3" ry="6.5"/><line x1="-6.5" y1="0" x2="6.5" y2="0"/></g></svg>
    <span>www.<span class="accent">vorledx</span>.com</span>
  </div>

</main>
</div>
</body>
</html>
```